Simple Business Card Design for Tavlo

Job:

Make a very simple, minimalist business card design with my details including adjusted logo. One side to be white (with logo & text). Other side to be yellow - try plain or with logo (or part of logo eg Z). Need business card to have continuity with website.

Logo:
Our logo is made from a free download font website:
http://www.typewell.net/search.php?q=rubber
but the spacing/kerning needs correcting/adjusting as the font spaces unevenly between letters (see attached files). Need logo to be very crisp/sharp when printed.

Printing:
We will be using Plika.com so the design needs to conform to their requirements, see here:

http://uk.plika.com/products/luxe/business-cards.html (scroll down for dimensions and guidelines)

Design:

must say "plant-based food consulting" underneath logo or somewhere
no address needed in contact section
sharp corners (not rounded)
one side white, one side yellow

name: Rosalind Whitcombe
1xmobile number: +44 7700900463
1xtwiiter: @brimcounsel
website address www.orchardtable.com
email address brim@orchardtable.com

Should be easy quick job, prompt + detailed feedback given, am online in UK 9am-10pm for next 3 days. Website is www.orchardtable.com

Industry/Entity Type

Business

Requirements
Must have
• The logo must be corrected. The kerning is not right.

Please use a warm-grey for text

Please submit in matt format, we will be printing matt finish.

Should not have
• Avoid using banners or curvy highlights

Please avoid using black

Please avoid submitting in gloss finish

```html
<!DOCTYPE html>
<html lang="en">
<head>
<meta charset="utf-8">
<title>Tavlo – Business Card</title>
<link rel="stylesheet" href="https://fonts.googleapis.com/css2?family=Josefin+Sans:wght@400;600;700&family=Special+Elite&display=swap">
<style>
  :root {
    --backdrop: #e8e5e0;
    --card-yellow: #f6ef6e;
    --card-white: #ffffff;
    --warm-grey: #6e6861;
    --logo-yellow: #f2e63a;
    --dot-grey: #c9c6c2;
    --card-shadow: rgba(60, 50, 40, 0.16);
  }
  * { margin: 0; padding: 0; box-sizing: border-box; }
  html, body {
    width: 1200px;
    height: 2320px;
    overflow: hidden;
    background: var(--backdrop);
  }
  .canvas {
    position: relative;
    width: 1200px;
    height: 2320px;
  }
  .card {
    position: absolute;
    left: 100px;
    width: 1000px;
    height: 647px;
    box-shadow: 0 10px 30px var(--card-shadow);
    overflow: hidden;
  }
  .card--back { top: 340px; background: var(--card-yellow); }
  .card--front { top: 1333px; background: var(--card-white); }

  .dot-field {
    position: absolute;
    width: 420px;
    height: 300px;
  }
  .card--back .dot-field {
    top: 0; right: 0;
    background: radial-gradient(ellipse at top right, rgba(255,255,255,0.95) 0%, rgba(255,255,255,0.55) 40%, rgba(255,255,255,0) 72%);
  }
  .card--front .dot-field {
    top: 0; left: 0;
    background: radial-gradient(ellipse at top left, var(--dot-grey) 0%, rgba(201,198,194,0.5) 40%, rgba(201,198,194,0) 72%);
  }

  .contact {
    position: absolute;
    left: 72px;
    bottom: 70px;
    color: var(--warm-grey);
  }
  .contact__name {
    font-family: "Special Elite", serif;
    font-size: 40px;
    letter-spacing: 1px;
    text-transform: uppercase;
    margin-bottom: 26px;
  }
  .contact__list { list-style: none; }
  .contact__item {
    display: flex;
    align-items: center;
    gap: 18px;
    font-family: "Josefin Sans", sans-serif;
    font-size: 22px;
    letter-spacing: 1.5px;
    text-transform: uppercase;
    height: 38px;
  }
  .contact__icon { width: 24px; height: 24px; flex: none; }

  .brand {
    position: absolute;
    right: 90px;
    top: 250px;
    text-align: left;
    color: var(--logo-yellow);
    font-family: "Josefin Sans", sans-serif;
  }
  .brand__name {
    font-weight: 700;
    font-size: 150px;
    line-height: 1;
    letter-spacing: 14px;
    text-transform: uppercase;
  }
  .brand__tagline {
    font-weight: 700;
    font-size: 24px;
    letter-spacing: 3px;
    text-transform: uppercase;
    margin-top: 8px;
  }
</style>
</head>
<body>
<main class="canvas">
  <section class="card card--back">
    <div class="dot-field" role="img" aria-label="Halftone dot pattern fading from the top right corner"></div>
    <div class="contact">
      <h1 class="contact__name">Rosalind Whitcombe</h1>
      <ul class="contact__list">
        <li class="contact__item">
          <svg class="contact__icon" viewBox="0 0 24 24"><rect x="6" y="2" width="12" height="20" rx="2" fill="none" stroke="var(--warm-grey)" stroke-width="2"/><circle cx="12" cy="18" r="1.3" fill="var(--warm-grey)"/></svg>
          <span>+44 7700900463</span>
        </li>
        <li class="contact__item">
          <svg class="contact__icon" viewBox="0 0 24 24"><rect x="2" y="5" width="20" height="14" fill="none" stroke="var(--warm-grey)" stroke-width="2"/><path d="M2 5 L12 13 L22 5" fill="none" stroke="var(--warm-grey)" stroke-width="2"/></svg>
          <span>brim@orchardtable.com</span>
        </li>
        <li class="contact__item">
          <svg class="contact__icon" viewBox="0 0 24 24"><rect x="3" y="3" width="18" height="18" fill="var(--warm-grey)"/></svg>
          <span>@brimcounsel</span>
        </li>
        <li class="contact__item">
          <svg class="contact__icon" viewBox="0 0 24 24"><circle cx="12" cy="12" r="9" fill="none" stroke="var(--warm-grey)" stroke-width="2"/><path d="M3 12 H21 M12 3 C8 8 8 16 12 21 M12 3 C16 8 16 16 12 21" fill="none" stroke="var(--warm-grey)" stroke-width="1.5"/></svg>
          <span>www.orchardtable.com</span>
        </li>
      </ul>
    </div>
  </section>

  <section class="card card--front">
    <div class="dot-field" role="img" aria-label="Halftone dot pattern fading from the top left corner"></div>
    <div class="brand">
      <div class="brand__name">Brim</div>
      <div class="brand__tagline">Plant-based food consulting</div>
    </div>
  </section>
</main>
</body>
</html>
```